New Business Card Design Project

I'd like a business card design around the same modern style that I used on my website www.brovanhs.com
It's gonna be one of those round corners double-sided business cards with maybe a big logo on the front and all the info on the back of the card.

Contact Information for Business Card

Marco Delgado
425-317-6084
www.brovanhs.com

www.facebook.com/BrovanHomeServices
www.intsgram.com/BrovanHomeServices

Requirements
Must have
• it needs to look elegant and modern

```html
<!DOCTYPE html>
<html lang="en">
<head>
<meta charset="utf-8">
<title>Brovan Home Services – Business Card</title>
<link href="https://fonts.googleapis.com/css2?family=Work+Sans:wght@400;500;700&display=swap" rel="stylesheet">
<style>
  :root {
    --bg: #161616;
    --card: #262626;
    --accent: #1a94dc;
    --text: #f2f2f2;
    --muted: #d8d8d8;
  }
  * { box-sizing: border-box; margin: 0; padding: 0; }
  html, body { width: 1200px; height: 900px; overflow: hidden; background: var(--bg); }
  body { font-family: "Work Sans", sans-serif; color: var(--text); position: relative; }

  .card {
    position: absolute;
    left: 270px;
    width: 660px;
    height: 377px;
    background: var(--card);
    border-bottom: 6px solid var(--accent);
    border-radius: 14px;
    overflow: hidden;
  }
  .card--front { top: 50px; }
  .card--back { top: 473px; }

  .brand {
    display: flex;
    align-items: center;
    gap: 14px;
  }
  .brand__mark {
    width: 22px; height: 22px;
    border-radius: 50%;
    background: var(--accent);
    flex: none;
  }
  .brand__name {
    font-weight: 700;
    color: var(--accent);
    line-height: 1.05;
  }

  .card--front .brand {
    position: absolute;
    inset: 0;
    justify-content: center;
  }
  .card--front .brand__name { font-size: 48px; }

  .card--back .brand {
    position: absolute;
    left: 44px;
    top: 135px;
    width: 300px;
  }
  .card--back .brand__name { font-size: 38px; }

  .divider {
    position: absolute;
    left: 372px;
    top: 60px;
    width: 2px;
    height: 250px;
    background: var(--accent);
  }

  .details {
    position: absolute;
    left: 400px;
    top: 62px;
    right: 20px;
  }
  .details__name {
    font-size: 28px;
    font-weight: 500;
    color: var(--accent);
    letter-spacing: 1.5px;
    text-transform: uppercase;
  }
  .details__role { font-size: 18px; color: var(--muted); margin-bottom: 14px; }
  .details__address { font-size: 15px; line-height: 1.35; margin-bottom: 10px; }
  .contact { list-style: none; font-size: 15px; line-height: 1.6; }
  .contact li { display: flex; align-items: center; gap: 9px; }
  .contact svg { width: 12px; height: 12px; flex: none; }
  .contact .dot { width: 10px; height: 10px; border-radius: 50%; background: var(--accent); flex: none; margin: 0 1px; }
</style>
</head>
<body>
  <section class="card card--front">
    <div class="brand">
      <span class="brand__mark"></span>
      <span class="brand__name">Brovan Home Services</span>
    </div>
  </section>

  <section class="card card--back">
    <div class="brand">
      <span class="brand__mark"></span>
      <span class="brand__name">Brovan Home Services</span>
    </div>
    <div class="divider"></div>
    <div class="details">
      <h1 class="details__name">Marco Delgado</h1>
      <p class="details__role">Director</p>
      <p class="details__address">2417 Harlow Ridge Road<br>Oklahoma City, OK 73012</p>
      <ul class="contact">
        <li>
          <svg viewBox="0 0 12 12"><path d="M3 1 L5 3.5 L4 5 Q5 7 7 8 L8.5 7 L11 9 L9.5 11 Q5 11 1 4.5 Q1 2 3 1Z" fill="none" stroke="#1a94dc" stroke-width="1.1"/></svg>
          425-317-6084
        </li>
        <li>
          <svg viewBox="0 0 12 12"><rect x="1" y="2.5" width="10" height="7" fill="none" stroke="#1a94dc" stroke-width="1.1"/><path d="M1 2.5 L6 6.5 L11 2.5" fill="none" stroke="#1a94dc" stroke-width="1.1"/></svg>
          Info@brovanhs.com
        </li>
        <li>
          <svg viewBox="0 0 12 12"><circle cx="6" cy="6" r="5" fill="none" stroke="#1a94dc" stroke-width="1.1"/><ellipse cx="6" cy="6" rx="2.2" ry="5" fill="none" stroke="#1a94dc" stroke-width="1"/><path d="M1 6 H11" stroke="#1a94dc" stroke-width="1"/></svg>
          www.brovanhs.com
        </li>
        <li><span class="dot"></span>/BrovanHomeServices</li>
        <li><span class="dot"></span>/BrovanHomeServices</li>
      </ul>
    </div>
  </section>
</body>
</html>
```